Stonebrace Business Card Design

The Stonebrace Co is an aggregate (crushing) equipment dealer serving Western Canadian provinces. Stonebrace is a distributor of aggregate equipment for different manufacturers.

We are looking to change and update the existing business card which has been used since the existence of the company. A copy of existing card has been attached for reference. The Stonebrace Co logo we want to remain the same and we want the green color to remain the same.

We are wanting something new with a different look. A refreshing card to show a new modern and updated look. No longer wanting to have the manufacturers on the back of the card but something more like our logo on the back of the card with a statement like "Aggregate Solutions"

ideas could be:
- card can be different colors on front and back
- front or reverse of the card could possibly be the green color with the logo in black

Target Market(s)

Owners of Aggregate/Crushing companies

Contact Information for Business Card

see above

Requirements
Must have
• - logo to remain same along with same font within logo
• - green color to remain same
Nice to have
• as noted above under project description
Should not have

```html
<!DOCTYPE html>
<html lang="en">
<head>
<meta charset="utf-8">
<title>Stonebrace Business Card</title>
<link href="https://fonts.googleapis.com/css2?family=Roboto:wght@400;500;700&display=swap" rel="stylesheet">
<style>
  :root {
    --backdrop: #7a5a40;
    --brand-green: #858a0a;
    --card-dark: #1d1e20;
    --ink-black: #1f1c1a;
    --text-light: #f2f2f2;
  }
  * { margin: 0; padding: 0; box-sizing: border-box; }
  html, body {
    width: 1200px;
    height: 960px;
    overflow: hidden;
  }
  body {
    position: relative;
    background: var(--backdrop);
    font-family: "Roboto", sans-serif;
  }
  .card {
    position: absolute;
    left: 320px;
    width: 600px;
    height: 340px;
    border-radius: 22px;
    box-shadow: 0 6px 14px rgba(0, 0, 0, 0.35);
  }
  .card-front {
    top: 108px;
    background: var(--brand-green);
  }
  .brand-dot {
    position: absolute;
    left: 196px;
    top: 157px;
    width: 34px;
    height: 34px;
    border-radius: 50%;
    background: var(--ink-black);
  }
  .brand-name {
    position: absolute;
    left: 248px;
    top: 159px;
    line-height: 30px;
    font-weight: 700;
    font-size: 23px;
    letter-spacing: 0.3px;
    color: var(--ink-black);
    white-space: nowrap;
  }
  .card-back {
    top: 494px;
    background: var(--card-dark);
    color: var(--text-light);
  }
  .back-line {
    position: absolute;
    left: 0;
    width: 100%;
    text-align: center;
    line-height: 24px;
    white-space: nowrap;
  }
  .back-brand {
    top: 84px;
    font-weight: 700;
    font-size: 20px;
    letter-spacing: 1px;
    color: var(--brand-green);
  }
  .person-name {
    top: 132px;
    font-weight: 500;
    font-size: 22px;
    color: var(--brand-green);
  }
  .person-title {
    top: 157px;
    font-weight: 500;
    font-size: 14px;
  }
  .address-line { top: 182px; font-size: 14px; }
  .phone-line { top: 205px; font-size: 14px; }
  .web-line { top: 225px; font-size: 14px; }
  .tagline {
    top: 247px;
    font-weight: 500;
    font-size: 15px;
    color: var(--brand-green);
  }
</style>
</head>
<body>
  <section class="card card-front">
    <span class="brand-dot"></span>
    <span class="brand-name">THE STONEBRACE CO.</span>
  </section>

  <section class="card card-back">
    <div class="back-line back-brand">STONEBRACE CO.</div>
    <div class="back-line person-name">BRENT MADSEN</div>
    <div class="back-line person-title">CEO/FOUNDER</div>
    <p class="back-line address-line">2215- 48B Avenue, Ridgeford, Alberta Z4R 2K7</p>
    <p class="back-line phone-line">P. 780.555.0142 M. 780.555.0187 F. 780.555.0163</p>
    <p class="back-line web-line">E. brent@stonebr.com W. www.stonebrace.ca</p>
    <p class="back-line tagline">Aggregate Solutions</p>
  </section>
</body>
</html>
```